Super elegant, crisp & clean Business card design required

We recently upgraded our branding - which is on our website - talvendoraphoto.com

I would like a simple, yet elegant, clean business card design please.

The font of my logo is Cinzel - and because of the natural colour - it's best to have this on a black background.

I would like to have the back of the business card - with simply my logo.

PLEASE DO NOT SUBMIT A COMPLICATED / UNCLEAN DESIGN

Industry/Entity Type

Business

Contact Information for Business Card

Talven Doroshko Photography

Font styles to use
Other font styles liked:
• Cinzel

Requirements
Must have
• A backpage with nothing but my logo
• Simple design - stands out
Should not have
• Colour that dont align with my logo
• Over complicated '/ non symmetrical design

```html
<!DOCTYPE html>
<html lang="en">
<head>
<meta charset="utf-8">
<title>Talven Doroshko Photography — Business Card</title>
<link rel="stylesheet" href="https://fonts.googleapis.com/css2?family=Cinzel:wght@400&family=Questrial&display=swap">
<style>
  :root {
    --page: #e9e7e3;
    --card-black: #0b0b0b;
    --card-white: #fbfbfa;
    --gold: #a8946e;
    --gold-soft: #b7a684;
  }
  * { box-sizing: border-box; margin: 0; padding: 0; }
  html, body {
    width: 1200px; height: 780px; overflow: hidden;
    background: var(--page);
  }
  .sheet {
    width: 1200px; height: 780px;
    display: flex; align-items: center; justify-content: center; gap: 60px;
  }
  .card {
    position: relative;
    width: 520px; height: 300px;
    background: var(--card-black);
    box-shadow: 0 10px 30px rgba(0,0,0,0.18);
    overflow: hidden;
  }
  .card-panel { position: absolute; inset: 0; width: 100%; height: 100%; }
  .card-panel path { fill: var(--card-white); }

  .brand {
    position: absolute;
    font-family: "Cinzel", serif;
    font-weight: 400;
    color: var(--gold);
    letter-spacing: 0.06em;
    display: flex; align-items: center; gap: 10px;
    white-space: nowrap;
  }
  .brand-dot {
    width: 8px; height: 8px; border-radius: 50%;
    background: var(--gold);
    flex: none;
  }
  .card-front .brand { top: 58px; right: 82px; font-size: 15px; }
  .card-back .brand {
    top: 50%; left: 50%; transform: translate(-50%, -50%);
    font-size: 17px;
  }

  .person {
    position: absolute; left: 82px; top: 168px;
    color: var(--gold);
  }
  .person-name {
    font-family: "Cinzel", serif;
    font-size: 20px; letter-spacing: 0.04em; line-height: 1.1;
  }
  .person-title {
    font-family: "Questrial", sans-serif;
    font-size: 13px; letter-spacing: 0.01em; margin-top: 2px;
  }

  .contact {
    position: absolute; left: 230px; top: 214px;
    list-style: none;
    font-family: "Questrial", sans-serif;
    font-size: 12.5px; line-height: 19px;
    color: var(--gold);
  }
  .contact li { display: flex; align-items: center; gap: 8px; }
  .contact-icon { width: 11px; height: 11px; flex: none; fill: var(--gold-soft); }
</style>
</head>
<body>
<main class="sheet">

  <section class="card card-front" aria-label="Business card front">
    <svg class="card-panel" viewBox="0 0 520 300" aria-hidden="true">
      <path d="M95,0 H425 Q545,150 425,300 H95 Q-25,150 95,0 Z"/>
    </svg>

    <div class="brand"><span class="brand-dot"></span>Talven Doroshko Photography</div>

    <div class="person">
      <p class="person-name">ARLEN VOSS</p>
      <p class="person-title">Chief Executive Officer</p>
    </div>

    <ul class="contact">
      <li>
        <svg class="contact-icon" viewBox="0 0 12 12" aria-hidden="true"><path d="M2.5 0.8 L4.3 0.5 L5.2 3.2 L3.9 4.1 Q4.8 6.6 7.2 7.9 L8.2 6.7 L11 7.6 L10.8 9.6 Q10 11.5 8.2 11 Q1.5 8.8 0.6 2.6 Q0.7 1.2 2.5 0.8 Z"/></svg>
        44 7700 900418
      </li>
      <li>
        <svg class="contact-icon" viewBox="0 0 12 12" aria-hidden="true"><path d="M0 2 H12 V10 H0 Z M1 3 L6 6.8 L11 3 V3 H1 Z" fill-rule="evenodd"/></svg>
        td.photography@lumenpost.com
      </li>
      <li>
        <svg class="contact-icon" viewBox="0 0 12 12" aria-hidden="true"><circle cx="6" cy="6" r="5.5"/><path d="M0.5 6 H11.5 M6 0.5 V11.5 M1.5 3.3 H10.5 M1.5 8.7 H10.5" stroke="#fbfbfa" stroke-width="0.7" fill="none"/><ellipse cx="6" cy="6" rx="2.4" ry="5.5" stroke="#fbfbfa" stroke-width="0.7" fill="none"/></svg>
        www.talvendoraphoto.com
      </li>
    </ul>
  </section>

  <section class="card card-back" aria-label="Business card back">
    <svg class="card-panel" viewBox="0 0 520 300" aria-hidden="true">
      <path d="M95,0 H425 Q545,150 425,300 H95 Q-25,150 95,0 Z"/>
    </svg>
    <div class="brand"><span class="brand-dot"></span>Talven Doroshko Photography</div>
  </section>

</main>
</body>
</html>
```